Corvane Freight Company Business Card Design

We are a company that delivers natural saltwater (from the ocean) to aquarium companies, restaurants and home marine tanks. I would like a new business card to suit.

Must include Name, company name, abn, contact number and website as well as logo (see attached).

Looking for a design that stands out, has a clean but unique appearance.

Double and single sided entries welcome

Business

• Logo

```html
<!DOCTYPE html>
<html lang="en">
<head>
<meta charset="utf-8">
<title>Corvane Freight Company – Business Card</title>
<link rel="stylesheet" href="https://fonts.googleapis.com/css2?family=Source+Sans+3:wght@400;600;700&display=swap">
<style>
  :root {
    --stage: #161616;
    --card-white: #ffffff;
    --sea-light: #55cbf4;
    --sea-deep: #1b5fae;
    --brand-blue: #1d8fd0;
    --name-blue: #1a62b0;
    --ink: #333333;
    --muted: #6b6b6b;
    --rule: #c9c9c9;
  }
  * { margin: 0; padding: 0; box-sizing: border-box; }
  html, body { width: 1200px; height: 420px; overflow: hidden; background: var(--stage); }
  body { font-family: "Source Sans 3", Arial, sans-serif; position: relative; }

  .card {
    position: absolute;
    top: 68px;
    width: 524px;
    height: 298px;
    border-radius: 18px;
    overflow: hidden;
  }
  .card--front { left: 69px; background: var(--card-white); }
  .card--back { left: 621px; background: var(--sea-light); }

  .front-waves { position: absolute; left: 0; bottom: 0; width: 524px; height: 60px; }

  .brand {
    position: absolute;
    display: flex;
    align-items: center;
    white-space: nowrap;
  }
  .brand__dot { border-radius: 50%; flex: none; }
  .brand__name { font-weight: 400; letter-spacing: -0.5px; }

  .brand--front { left: 40px; top: 120px; gap: 8px; }
  .brand--front .brand__dot { width: 14px; height: 14px; background: var(--brand-blue); }
  .brand--front .brand__name { font-size: 34px; color: var(--brand-blue); }

  .brand--back { left: 58px; top: 122px; gap: 14px; }
  .brand--back .brand__dot { width: 26px; height: 26px; background: var(--card-white); }
  .brand--back .brand__name { font-size: 58px; color: var(--card-white); }

  .divider {
    position: absolute;
    left: 312px;
    top: 46px;
    width: 1px;
    height: 174px;
    background: var(--rule);
  }

  .contact { position: absolute; left: 329px; top: 48px; color: var(--ink); font-size: 13.5px; line-height: 19px; }
  .contact__name { font-size: 18px; font-weight: 700; color: var(--name-blue); line-height: 22px; }
  .contact__title { font-size: 15px; color: var(--muted); line-height: 20px; margin-bottom: 12px; }
  .contact__row { display: flex; align-items: center; gap: 7px; }
  .contact__row svg { width: 11px; height: 11px; flex: none; }
  .contact__address { margin-top: 12px; }
  .contact__abn { margin-top: 12px; }
</style>
</head>
<body>

<section class="card card--front" aria-label="Business card front">
  <div class="brand brand--front">
    <span class="brand__dot"></span>
    <span class="brand__name">Corvane Freight</span>
  </div>

  <div class="divider"></div>

  <div class="contact">
    <p class="contact__name">Your Name</p>
    <p class="contact__title">Title</p>
    <p class="contact__row">
      <svg viewBox="0 0 12 12" aria-hidden="true"><circle cx="6" cy="6" r="5.3" fill="none" stroke="#333" stroke-width="1.1"/><path d="M4 3.2c-.6.4-.7 1.3-.2 2.4.6 1.3 1.7 2.5 2.9 3 .8.3 1.4.1 1.7-.4l-1.1-1-.7.4c-.6-.3-1.2-1-1.5-1.6l.4-.7-1-1.1z" fill="#333"/></svg>
      123-456-7892
    </p>
    <p class="contact__row">
      <svg viewBox="0 0 12 12" aria-hidden="true"><circle cx="6" cy="6" r="5.2" fill="none" stroke="#333" stroke-width="1.1"/><ellipse cx="6" cy="6" rx="2.2" ry="5.2" fill="none" stroke="#333" stroke-width="1"/><path d="M1 6h10M1.8 3.5h8.4M1.8 8.5h8.4" stroke="#333" stroke-width="0.9"/></svg>
      www.corvanefreight.com
    </p>
    <p class="contact__address">Street Name, City Name<br>State, Zip Code</p>
    <p class="contact__abn">ABN: 123456789</p>
  </div>

  <svg class="front-waves" viewBox="0 0 524 60" preserveAspectRatio="none" aria-hidden="true">
    <path d="M0 12 C120 40 260 14 380 14 C450 14 500 22 524 40 L524 60 L0 60 Z" fill="var(--sea-deep)"/>
    <path d="M0 22 C130 48 270 22 390 22 C455 22 505 32 524 46 L524 60 L0 60 Z" fill="var(--card-white)"/>
    <path d="M0 28 C130 54 270 28 390 26 C455 26 505 36 524 50 L524 60 L0 60 Z" fill="var(--sea-light)"/>
  </svg>
</section>

<section class="card card--back" aria-label="Business card back">
  <div class="brand brand--back">
    <span class="brand__dot"></span>
    <span class="brand__name">Corvane Freight</span>
  </div>
</section>

</body>
</html>
```